Velk Partners Building Business Cards

We need a business card that reflects our business as "Solar Experts" in San Diego. Browse our website www.velkpartners.example our License needs to be displayed as "CSLB# 3867140" our phone number is (619) 555-0187

Save thousands on your electric bills and increase the value of your home while helping to protect the environment. Our solar installation experts will help you design the system that's right for you, using only the highest quality equipment that will look great and give you ideal performance. Our goal is to make you energy independent, and get your electric bill to 0.

Paul Osterby
(619) 555-0187
paul@velkpartners.example

Target Market(s)

Home owners in san diego looking for solar

Industry/Entity Type

Solar Energy

Contact Information for Business Card

Paul Osterby
(619) 555-0187
paul@velkpartners.example

Font styles to use
Other font styles liked:
• Use our logo font

Requirements
Must have
• License needs to be displayed as "CSLB# 3867140" our phone number is (619) 555-0187
Nice to have
• Real images of rooftop home solar in san diego
Should not have
• our business address

```html
<!DOCTYPE html>
<html lang="en">
<head>
<meta charset="utf-8">
<title>Velk Partners Building – Business Cards</title>
<link rel="stylesheet" href="https://fonts.googleapis.com/css2?family=Montserrat:wght@600;800&family=Open+Sans:wght@400;600&display=swap">
<style>
  :root {
    --navy: #1a3a72;
    --orange: #f6a800;
    --white: #ffffff;
    --backdrop: #e8ebec;
    --card-shadow: 0 10px 24px rgba(20, 30, 50, 0.18);
  }
  * { box-sizing: border-box; margin: 0; padding: 0; }
  html, body {
    width: 1200px; height: 812px; overflow: hidden;
    background: var(--backdrop);
  }
  .stage { position: relative; width: 1200px; height: 812px; }
  .card {
    position: absolute; width: 540px; height: 309px;
    box-shadow: var(--card-shadow); overflow: hidden;
  }

  /* Back of card */
  .card-back {
    left: 40px; top: 200px; background: var(--navy);
    display: flex; flex-direction: column; align-items: center; justify-content: center;
  }
  .brand-lockup { display: flex; align-items: center; gap: 14px; }
  .brand-dot { width: 34px; height: 34px; border-radius: 50%; background: var(--orange); }
  .brand-name-back {
    font-family: "Montserrat", sans-serif; font-weight: 800;
    font-size: 30px; color: var(--white); letter-spacing: -0.5px;
  }
  .back-web {
    margin-top: 46px;
    font-family: "Open Sans", sans-serif; font-size: 13px;
    letter-spacing: 2.4px; color: var(--white); text-transform: uppercase;
  }

  /* Front of card */
  .card-front { left: 620px; top: 300px; background: var(--white); }
  .front-band { position: absolute; inset: 0; }
  .brand-name-front {
    position: absolute; left: 34px; top: 108px; width: 250px;
    font-family: "Montserrat", sans-serif; font-weight: 800;
    font-size: 26px; line-height: 1.12; color: var(--navy); letter-spacing: -0.5px;
  }
  .person { position: absolute; left: 110px; top: 222px; font-family: "Montserrat", sans-serif; }
  .person-name { font-weight: 800; font-size: 19px; color: var(--navy); letter-spacing: 0.3px; }
  .person-title { font-weight: 600; font-size: 14px; color: var(--orange); margin-top: 2px; }
  .contact-list {
    position: absolute; right: 12px; top: 98px; list-style: none;
    font-family: "Open Sans", sans-serif; font-size: 11.5px; color: var(--white);
    line-height: 1.8;
  }
  .contact-list li { display: flex; justify-content: flex-end; align-items: center; gap: 6px; white-space: nowrap; }
  .contact-icon { width: 11px; height: 11px; flex: none; }
  .contact-icon.spacer { visibility: hidden; }
</style>
</head>
<body>
<main class="stage">

  <section class="card card-back" aria-label="Business card back">
    <div class="brand-lockup">
      <span class="brand-dot"></span>
      <span class="brand-name-back">Velk Partners Building</span>
    </div>
    <p class="back-web">www.velkpartners.example</p>
  </section>

  <section class="card card-front" aria-label="Business card front">
    <svg class="front-band" viewBox="0 0 540 309" width="540" height="309" aria-hidden="true">
      <path d="M400 0 C330 64 310 200 350 309 L540 309 L540 0 Z" fill="var(--navy)"/>
      <path d="M390 0 C318 64 296 196 332 300" fill="none" stroke="var(--orange)" stroke-width="3"/>
    </svg>

    <p class="brand-name-front">Velk Partners Building</p>

    <div class="person">
      <p class="person-name">PAUL OSTERBY</p>
      <p class="person-title">CEO/FOUNDER</p>
    </div>

    <ul class="contact-list">
      <li>CSLB# 3867140<svg class="contact-icon spacer" viewBox="0 0 12 12"></svg></li>
      <li>(619) 555-0187
        <svg class="contact-icon" viewBox="0 0 12 12" aria-hidden="true"><path d="M3 1 L5 3.5 L4 5 C4.8 6.6 5.6 7.4 7 8 L8.5 7 L11 9 L9.5 11 C5 10.5 1.5 7 1 2.5 Z" fill="var(--orange)"/></svg>
      </li>
      <li>paul@velkpartners.example
        <svg class="contact-icon" viewBox="0 0 12 12" aria-hidden="true"><rect x="0.5" y="2.5" width="11" height="7.5" fill="var(--orange)"/><path d="M0.5 2.5 L6 7 L11.5 2.5" fill="none" stroke="var(--navy)" stroke-width="1"/></svg>
      </li>
      <li>www.velkpartners.example
        <svg class="contact-icon" viewBox="0 0 12 12" aria-hidden="true"><circle cx="6" cy="6" r="5.5" fill="var(--orange)"/><path d="M6 0.5 V11.5 M0.5 6 H11.5 M6 0.5 C3 3 3 9 6 11.5 M6 0.5 C9 3 9 9 6 11.5" fill="none" stroke="var(--navy)" stroke-width="0.8"/></svg>
      </li>
    </ul>
  </section>

</main>
</body>
</html>
```